Coolant Fluid for Radiator ZEPH RUNE®

Its my first time working with Artbazaar, and I want to see how it goes:)

We are needing a New exotic label design for our Zeph Rune ® Coolant Fluid for Radiators. Label if possible should be in

Spanish, but its ok if it is in English as we can edit the text later. This label should really stand out!

Front side of label:
Brand Name is ZEPH RUNE®

It's a Red Type Radiator Fluid/ Liquid. ( This Should Stand out)

It's also Triple action as it works as a Coolant,Anti Rust and Corrosion Inhibitor. It also Protects Aluminuim (Motor Block)

Its Special Red type and chemical composition help mantain the temperature at an optimum level thus preventing Overheating.

Bottle Capacity is 1 liter (Should be on front Label Bottom Right Side)

Back Side of Label:

Properties:
**Emphasizing that the product's Special Red type and chemical composition help mantain the temperature at an optimum

level thus preventing Overheating.
**Emphasize Triple Action (Mentioned above....)
**Will protect Plastic parts, and Connections.
**Mantain Low temperature.
**Prevent and Eliminate Build up of Calcium.

Instruction to use:
1. fill Radiator with ZEPH RUNE®
2. fill and Mix with Destilled water.

Dosing:
Small Cars 1Liter
Medium Cars 1Liter
Heavy Cars+Heavy Machinery 3Liter

As with almost all fluids for vehicles etc..Label should include safety Hazards.
Such as NFPA label (Please google it) ( Red Blue yellow and White ) Blue box should have a 1 and the others a Zero.

Health and Safety Hazards:
*If swallowed do not Induce vomiting
*seek for medical attention
*Poisonous if consumed
*Keep out of reach of children
(We will add some other things, that we are required to add)
Hazard Symbol Emphazising to read the manufacturer Instructions..

And a Small place where we can place a Barcode/ Recycable Symbol and Dispose of..
Product Registry Code, and Produced and Distributed by Lorem Ipsum etc..

I have attached some Bottle Designs,but dont Restrict yourself on these Bottles, Please keep in mind that the Bottle neck will be placed in the middle of the bottle and not to the sides as with most standard Oil Bottles.
If you have a better Idea/Outline of another bottle dont Hesitate to make a suggestion!

Thanks!
And Sorry my English is not the best :)
hope you have fun Designing this new Label!
Updates

Designs should be a little more something like these.. Please check the gallery, I uploaded some samples.. http://snapvault.example/gallery/qk48w2r7/ These are just for reference.. Regards,

Hi, Please Don't limit yourself to to the shape of the label. If you Think another shape would be better, please do. I will create a special bottle for your label. Thanks!

```html
<!DOCTYPE html>
<html lang="en">
<head>
<meta charset="utf-8">
<title>ZEPH RUNE® Red Type Radiator Fluid – Label</title>
<link rel="stylesheet" href="https://fonts.googleapis.com/css2?family=Lato:wght@400;700;900&family=Michroma&family=Tinos&display=swap">
<style>
  :root {
    --label-red: #e31b23;
    --label-red-deep: #b3121c;
    --label-red-dark: #8b0a18;
    --accent-yellow: #ffe400;
    --soft-pink: #f3d2d2;
    --muted-pink: #e89a9a;
    --white: #ffffff;
    --ink: #111111;
    --nfpa-red: #ee2a2a;
    --nfpa-blue: #7a7fc2;
    --nfpa-yellow: #f2ea1c;
    --nfpa-white: #ffffff;
    --recycle-green: #3fae3a;
    --page: #ffffff;
  }
  html, body {
    margin: 0;
    padding: 0;
    width: 1200px;
    height: 1056px;
    overflow: hidden;
    background: var(--page);
  }
  .label-sheet {
    display: block;
    width: 1200px;
    height: 1056px;
  }
  .brand { font-family: "Lato", sans-serif; font-weight: 900; fill: var(--white); }
  .tagline { font-family: "Michroma", sans-serif; fill: var(--white); }
  .benefit { font-family: "Lato", sans-serif; fill: var(--accent-yellow); }
  .feature { font-family: "Lato", sans-serif; fill: var(--soft-pink); }
  .description { font-family: "Lato", sans-serif; fill: var(--muted-pink); }
  .capacity { font-family: "Lato", sans-serif; fill: var(--white); }
  .body-copy { font-family: "Lato", sans-serif; fill: var(--white); }
  .instructions { font-family: "Lato", sans-serif; fill: var(--accent-yellow); }
  .nfpa-text { font-family: "Tinos", serif; fill: var(--ink); }
  .side-caption { font-family: "Lato", sans-serif; fill: var(--ink); }
</style>
</head>
<body>
<svg class="label-sheet" viewBox="0 0 932 818" preserveAspectRatio="none" xmlns="http://www.w3.org/2000/svg">
  <defs>
    <linearGradient id="label-fill" x1="0" y1="0" x2="0.4" y2="1">
      <stop offset="0" stop-color="var(--label-red)"/>
      <stop offset="0.6" stop-color="#d8141f"/>
      <stop offset="1" stop-color="var(--label-red-deep)"/>
    </linearGradient>
    <linearGradient id="swoosh-fill" x1="0" y1="0" x2="1" y2="0">
      <stop offset="0" stop-color="#ffffff" stop-opacity="0.35"/>
      <stop offset="0.5" stop-color="#ffffff" stop-opacity="0.12"/>
      <stop offset="1" stop-color="#ffb347" stop-opacity="0.45"/>
    </linearGradient>
    <path id="panel-outline" d="M10,745 L10,490 C40,380 70,150 125,55 C170,20 240,2 305,0 C350,0 380,10 400,20 C395,120 420,260 435,365 L435,665 C330,690 120,700 10,745 Z"/>
    <clipPath id="front-clip"><use href="#panel-outline"/></clipPath>
    <clipPath id="back-clip"><use href="#panel-outline" transform="translate(932,0) scale(-1,1)"/></clipPath>
  </defs>

  <!-- Front panel -->
  <g class="panel-front">
    <use href="#panel-outline" fill="url(#label-fill)"/>
    <g clip-path="url(#front-clip)">
      <path class="swoosh" d="M40,300 C160,380 260,380 440,380 L440,470 C300,470 160,470 60,520 C80,440 60,360 40,300 Z" fill="url(#swoosh-fill)"/>
      <path class="lower-band" d="M0,560 C150,520 300,540 440,520 L440,760 L0,760 Z" fill="#000000" fill-opacity="0.12"/>
      <path class="base-shade" d="M0,680 C150,650 300,660 440,640 L440,760 L0,760 Z" fill="#000000" fill-opacity="0.12"/>
    </g>
    <text class="brand" x="265" y="265" font-size="42" text-anchor="middle">ZEPH RUNE®</text>
    <text class="tagline" x="255" y="304" font-size="10.5" text-anchor="middle">Red Type Radiator Fluid/ Liquid</text>
    <g class="benefit" font-size="17" text-anchor="end">
      <text x="357" y="362">Works as a</text>
      <text x="357" y="385">Coolant</text>
      <text x="357" y="407">Anti Rust &amp;</text>
      <text x="357" y="429">Corrosion Inhibitor</text>
    </g>
    <text class="feature" x="62" y="582" font-size="16">Protects Aluminuim (Motor Block)</text>
    <g class="description" font-size="12">
      <text x="62" y="617">Its Special Red type and chemical</text>
      <text x="62" y="632">composition help mantain the</text>
      <text x="62" y="647">temperature at an optimum level</text>
      <text x="62" y="662">thus preventing Overheating</text>
    </g>
    <text class="capacity" x="323" y="637" font-size="20">1 liter</text>
  </g>

  <!-- Back panel -->
  <g class="panel-back">
    <use href="#panel-outline" transform="translate(932,0) scale(-1,1)" fill="url(#label-fill)"/>
    <g clip-path="url(#back-clip)">
      <path class="swoosh" d="M890,260 C780,380 680,380 490,390 L490,480 C640,480 780,480 880,540 C860,450 880,360 890,260 Z" fill="url(#swoosh-fill)"/>
      <path class="lower-band" d="M480,560 C640,530 780,540 940,520 L940,760 L480,760 Z" fill="#000000" fill-opacity="0.12"/>
      <path class="base-shade" d="M480,680 C640,650 780,660 940,640 L940,760 L480,760 Z" fill="#000000" fill-opacity="0.12"/>
    </g>
    <text class="brand" x="537" y="114" font-size="20">ZEPH RUNE®</text>

    <g class="body-copy properties" font-size="9">
      <text x="541" y="184">Properties:</text>
      <text x="541" y="195">**Emphasizing that the product's Special Red type</text>
      <text x="541" y="207">and chemical composition help mantain the</text>
      <text x="541" y="219">temperature at an optimum</text>
      <text x="541" y="244">level thus preventing Overheating.</text>
      <text x="541" y="256">**Emphasize Triple Action</text>
      <text x="541" y="268">**Will protect Plastic parts, and Connections.</text>
      <text x="541" y="280">**Mantain Low temperature.</text>
      <text x="541" y="292">**Prevent and Eliminate Build up of Calcium.</text>
    </g>

    <rect class="instructions-box" x="612" y="320" width="224" height="120" fill="var(--label-red-dark)"/>
    <g class="instructions" font-size="9">
      <text x="639" y="334">Instruction to use:</text>
      <text x="639" y="346">1. fill Radiator with ZEPH RUNE®</text>
      <text x="639" y="358">2. fill and Mix with Destilled water.</text>
      <text x="639" y="382">Dosing:</text>
      <text x="639" y="395">Small Cars 1Liter</text>
      <text x="639" y="407">Medium Cars 1Liter</text>
      <text x="639" y="419">Heavy Cars+Heavy Machinery 3Liter</text>
    </g>

    <g class="body-copy hazards" font-size="9" text-anchor="end">
      <text x="713" y="469">Health and Safety Hazards:</text>
      <text x="713" y="481">*If swallowed do not Induce vomiting</text>
      <text x="713" y="493">*seek for medical attention</text>
      <text x="713" y="505">*Poisonous if consumed</text>
      <text x="713" y="517">*Keep out of reach of children</text>
    </g>

    <g class="nfpa-diamond" stroke="#ffffff" stroke-width="1">
      <polygon points="808,444 852,488 808,532 764,488" fill="var(--nfpa-red)"/>
      <polygon points="764,488 808,532 764,576 720,532" fill="var(--nfpa-blue)"/>
      <polygon points="852,488 896,532 852,576 808,532" fill="var(--nfpa-yellow)"/>
      <polygon points="808,532 852,576 808,620 764,576" fill="var(--nfpa-white)"/>
    </g>
    <g class="nfpa-text" font-size="11" text-anchor="middle">
      <text x="808" y="480">Red</text>
      <text x="808" y="493">flammability</text>
      <text x="764" y="525">Blue</text>
      <text x="764" y="538">health</text>
      <text x="852" y="525">Yellow</text>
      <text x="852" y="538">reactivity</text>
      <text x="808" y="568">White</text>
      <text x="808" y="581">special</text>
    </g>

    <circle class="recycle-mark" cx="668" cy="648" r="11" fill="var(--recycle-green)"/>

    <g class="body-copy disposal" font-size="5">
      <text x="802" y="638">Dispose of..</text>
      <text x="802" y="646">Product Registry Code, and Produced</text>
      <text x="802" y="654">and Distributed by Lorem Ipsum etc.</text>
    </g>
  </g>

  <text class="side-caption" x="201" y="774" font-size="12" text-anchor="middle">FRONT</text>
  <text class="side-caption" x="714" y="774" font-size="12" text-anchor="middle">BACK</text>
</svg>
</body>
</html>
```